I need a business card designed using the logo provided either vertical or horizontal......Harbourline Property Group is an Australian based real estate company that caters for the upper end of the market so the design of the business card "must reflect" the companies image!!
Colour combinations are optional but "must be realistic" and must be able to be accurately useable CMYK colours.
Please consider that any colours used "must be able to be used" and be suitable in following designs for "pull out banner signs" and "real estate signs".
The colours and the font in the attached designs are for example and other combinations are encouraged.
Target Market(s)
The High End of the Australian real estate market
Industry/Entity Type
Business
Contact Information for Business Card
Logo - Business Name - Director + Licensed Real Estate Agent - Mobile Number (Cell Phone) - Business Number - Fax - Email Address - Web address
Requirements
Must have
- Designs and colours (CMYK) that can easily be interpreted by an Australian printer.
Nice to have
- Some alternative ideas on colour and font..........the ones provided are ok and have been provided as an example but I am looking for alternative ideas
Should not have
- Loud, overly bright colours. Designs that do not reflect the professional standards of the business.
- Designs that look good on a computer monitor but can not be re-created on a printing press.............this is most important when it comes to shading etc.

```html
<!DOCTYPE html>
<html lang="en">
<head>
<meta charset="utf-8">
<title>Harbourline Property Group – Business Card</title>
<link rel="stylesheet" href="https://fonts.googleapis.com/css2?family=Lato:wght@400;700&display=swap">
<style>
  :root {
    --backdrop: #3a312c;
    --card-black: #0d0d0d;
    --card-black-edge: #161616;
    --gold: #d39a2c;
    --gold-pale: #e6d3a0;
    --silver: #b9b9b9;
    --ink-white: #f2f2f2;
  }
  * { box-sizing: border-box; margin: 0; padding: 0; }
  html, body {
    width: 1200px;
    height: 844px;
    overflow: hidden;
    background: var(--backdrop);
    font-family: "Lato", Arial, sans-serif;
  }
  .sheet {
    width: 1200px;
    height: 844px;
    display: flex;
    align-items: center;
    justify-content: center;
    gap: 60px;
  }
  .card {
    width: 520px;
    height: 300px;
    background: linear-gradient(135deg, var(--card-black-edge), var(--card-black));
    box-shadow: 0 10px 30px rgba(0,0,0,0.45);
    position: relative;
  }
  /* Front: contact side */
  .card-front .brand {
    position: absolute;
    left: 44px;
    top: 112px;
    width: 190px;
    display: flex;
    align-items: flex-start;
    gap: 12px;
  }
  .brand-square {
    width: 14px;
    height: 14px;
    background: var(--gold);
    flex: none;
    margin-top: 6px;
  }
  .brand-name {
    color: var(--gold-pale);
    font-weight: 700;
    font-size: 22px;
    line-height: 1.2;
    letter-spacing: 0.5px;
  }
  .contact {
    position: absolute;
    left: 290px;
    top: 52px;
    width: 220px;
  }
  .contact-name {
    color: var(--gold);
    font-size: 20px;
    font-weight: 400;
    line-height: 1.1;
  }
  .contact-role {
    color: var(--ink-white);
    font-size: 12.5px;
    margin-top: 2px;
  }
  .contact-address {
    color: var(--ink-white);
    font-size: 13.5px;
    line-height: 1.3;
    margin-top: 16px;
  }
  .contact-lines {
    list-style: none;
    color: var(--gold);
    font-size: 13.5px;
    line-height: 1.35;
    margin-top: 18px;
  }
  .contact-lines .label { color: var(--gold); }
  .contact-lines .value { color: var(--ink-white); }
  /* Back: brand side */
  .card-back {
    display: flex;
    align-items: center;
    justify-content: center;
  }
  .card-back .brand {
    display: flex;
    align-items: center;
    gap: 14px;
  }
  .card-back .brand-square { margin-top: 0; width: 18px; height: 18px; }
  .card-back .brand-name {
    color: var(--silver);
    font-weight: 400;
    font-size: 24px;
    letter-spacing: 1.5px;
    text-transform: uppercase;
  }
</style>
</head>
<body>
  <main class="sheet">
    <section class="card card-front">
      <div class="brand">
        <span class="brand-square"></span>
        <span class="brand-name">Harbourline Property Group</span>
      </div>
      <div class="contact">
        <p class="contact-name">Marcus Ellory</p>
        <p class="contact-role">Managing Director</p>
        <p class="contact-address">48 Wharf Street, Pyrmont<br>Sydney NSW, 2009.</p>
        <ul class="contact-lines">
          <li><span class="label">T:</span> <span class="value">044-218 730 915</span></li>
          <li><span class="label">E:</span> <span class="value">hello@harbourline.com</span></li>
          <li><span class="label">W:</span><span class="value">www.harbourline.com</span></li>
        </ul>
      </div>
    </section>
    <section class="card card-back">
      <div class="brand">
        <span class="brand-square"></span>
        <span class="brand-name">Harbourline Property Group</span>
      </div>
    </section>
  </main>
</body>
</html>
```